Building technology company seek stationery design and folder design

Letterhead, and a folder design
ideally, I would have two letter head design, one is for one-page bussiness letter. the other one I can use for longer document such report, or analysis regular report page
you can find company logo and overall style at our website:
www.structavolt.example

we are in building technology business, using internet of things technology to improve building energy efficiency to make building greener.

Industry/Entity Type

It Company

Requirements
Must have
• company logo
Nice to have
• techy look abstract graphics, etc.
Should not have
• no comment

```html
<!DOCTYPE html>
<html lang="en">
<head>
<meta charset="utf-8">
<title>Structavolt – Proposal Cover</title>
<link rel="stylesheet" href="https://fonts.googleapis.com/css2?family=Roboto:wght@400;500&display=swap">
<style>
  :root {
    --backdrop: #5e5d6a;
    --paper: #ffffff;
    --ink-dark: #0a1d20;
    --lime: #a6ce39;
    --lime-deep: #9dbf3a;
    --muted: #8b9188;
    --footer-text: #ffffff;
  }
  * { margin: 0; padding: 0; box-sizing: border-box; }
  html, body {
    width: 1200px;
    height: 992px;
    overflow: hidden;
    background: var(--backdrop);
    font-family: "Roboto", Arial, sans-serif;
  }
  .cover {
    position: absolute;
    left: 252px;
    top: 26px;
    width: 696px;
    height: 940px;
    background: var(--paper);
    overflow: hidden;
  }
  .cover__waves {
    position: absolute;
    inset: 0;
    width: 100%;
    height: 100%;
  }
  .brand {
    position: absolute;
    right: 50px;
    top: 126px;
    font-size: 34px;
    font-weight: 500;
    letter-spacing: 3px;
    color: var(--lime);
    line-height: 1;
  }
  .proposal {
    position: absolute;
    left: 0;
    right: 0;
    top: 554px;
    text-align: center;
  }
  .proposal__title {
    font-size: 45px;
    font-weight: 500;
    color: var(--lime);
    line-height: 1;
  }
  .proposal__subtitle {
    margin-top: 6px;
    font-size: 18px;
    font-weight: 400;
    color: var(--muted);
    line-height: 1.2;
  }
  .contact-bar {
    position: absolute;
    left: 0;
    right: 0;
    bottom: 0;
    height: 32px;
    background: var(--lime);
    display: flex;
    align-items: center;
    justify-content: center;
    gap: 8px;
    font-size: 10.5px;
    font-weight: 500;
    color: var(--footer-text);
  }
  .contact-bar__item {
    display: flex;
    align-items: center;
    gap: 5px;
  }
  .contact-bar__icon { width: 9px; height: 9px; fill: var(--footer-text); }
</style>
</head>
<body>
  <main class="cover">
    <svg class="cover__waves" viewBox="0 0 614 829" preserveAspectRatio="none" aria-hidden="true">
      <path fill="var(--lime)" d="M0,0 C90,30 160,110 210,153 C290,215 380,255 535,262 C570,250 600,225 614,205 L614,829 L0,829 Z"/>
      <path fill="var(--lime-deep)" d="M0,35 C100,70 170,140 230,178 C300,222 380,262 530,262 L614,258 L614,829 L0,829 Z"/>
      <path fill="var(--ink-dark)" d="M0,162 C60,145 130,130 200,150 C290,180 360,290 440,290 C520,290 570,262 614,255 L614,829 L0,829 Z"/>
    </svg>

    <div class="brand">STRUCTAVOLT</div>

    <section class="proposal">
      <h1 class="proposal__title">TITLE FOR PROPOSAL</h1>
      <p class="proposal__subtitle">Lorem Ipsum is simply dummy text of the printing</p>
    </section>

    <footer class="contact-bar">
      <span class="contact-bar__item">
        <svg class="contact-bar__icon" viewBox="0 0 24 24"><path d="M6.6 10.8a15.1 15.1 0 0 0 6.6 6.6l2.2-2.2a1 1 0 0 1 1-.25 11.4 11.4 0 0 0 3.6.57 1 1 0 0 1 1 1V20a1 1 0 0 1-1 1A17 17 0 0 1 3 4a1 1 0 0 1 1-1h3.5a1 1 0 0 1 1 1c0 1.25.2 2.45.57 3.6a1 1 0 0 1-.25 1z"/></svg>
        (555) 014-2290
      </span>
      <span class="contact-bar__item">
        <svg class="contact-bar__icon" viewBox="0 0 24 24"><path d="M2 5h20v14H2z M4 7v1l8 5 8-5V7l-8 5z" fill-rule="evenodd"/></svg>
        info@structavolt.example
      </span>
      <span class="contact-bar__item">
        <svg class="contact-bar__icon" viewBox="0 0 24 24"><path d="M12 2a10 10 0 1 0 0 20 10 10 0 0 0 0-20zm0 2c1.2 0 2.6 2.4 2.9 7H9.1C9.4 6.4 10.8 4 12 4zm-2.9 9h5.8c-.3 4.6-1.7 7-2.9 7s-2.6-2.4-2.9-7zM4.1 11a8 8 0 0 1 3.2-5.6A14 14 0 0 0 7.1 11zm0 2h3a14 14 0 0 0 .2 5.6A8 8 0 0 1 4.1 13zm12.8 0h3a8 8 0 0 1-3.2 5.6 14 14 0 0 0 .2-5.6zm0-2a14 14 0 0 0-.2-5.6A8 8 0 0 1 19.9 11z"/></svg>
        www.structavolt.example
      </span>
    </footer>
  </main>
</body>
</html>
```